Roofing company in Toronto, Canada needs a logo design and business card design

We need a business card and logo created for our company. Our company is "KLV Roofing" which provides roofing services for commercial and residential customers. We serve customers in the Greater Toronto Area (in Canada) thus the name KLV.

We want the logo and business card to be a modern design displaying professionalism and quality in the work. We would prefer rounded corners for the business cards but are open to other ideas. The cards should be pleasant and appealing to customers.

Target Market(s)

Commercial and Residential customers

Industry/Entity Type

Roofing

Contact Information for Business Card

Logo Text

KLV Roofing

Requirements
Nice to have
• Colours that are pleasing to the eye but at the same time should stand out from other business cards. If the design can incorporate the name of KLV Roofing and the actual concept of roofing that would be nice.
Should not have
• Do not want the business cards or logo to be childish looking. Need to look professionally designed.

```html
<!DOCTYPE html>
<html lang="en">
<head>
<meta charset="utf-8">
<title>KLV Roofing – Business Card</title>
<link href="https://fonts.googleapis.com/css2?family=Lato:wght@400;700;900&display=swap" rel="stylesheet">
<style>
  :root {
    --stage: #e9e7e4;
    --card-black: #0b0b0b;
    --card-white: #ffffff;
    --brand-red: #e3202a;
    --text-light: #ffffff;
    --text-dark: #111111;
  }
  * { box-sizing: border-box; margin: 0; padding: 0; }
  html, body { width: 1200px; height: 780px; overflow: hidden; }
  body {
    background: var(--stage);
    font-family: "Lato", sans-serif;
    position: relative;
  }
  .card {
    position: absolute;
    top: 235px;
    width: 540px;
    height: 310px;
    border-radius: 10px;
    overflow: hidden;
    box-shadow: 0 6px 18px rgba(0,0,0,0.18);
  }
  .card--front { left: 45px; background: var(--card-black); }
  .card--back { left: 615px; background: var(--card-white); }

  .brand {
    position: absolute;
    display: flex;
    align-items: center;
    gap: 12px;
    font-weight: 900;
    letter-spacing: 1px;
    white-space: nowrap;
  }
  .brand__mark {
    width: 30px;
    height: 30px;
    background: var(--brand-red);
    flex: none;
  }
  .card--front .brand {
    left: 50%; top: 50%;
    transform: translate(-50%, -50%);
    font-size: 44px;
    color: var(--text-light);
  }
  .card--back .brand {
    left: 28px; top: 132px;
    gap: 10px;
    font-size: 25px;
    color: var(--text-dark);
  }
  .card--back .brand__mark { width: 19px; height: 19px; }

  .card__wave { position: absolute; inset: 0; width: 540px; height: 310px; }

  .contact {
    position: absolute;
    left: 352px;
    top: 62px;
    color: var(--text-light);
  }
  .contact__name {
    font-size: 17px;
    font-weight: 900;
    letter-spacing: 0.5px;
    text-transform: uppercase;
    line-height: 1;
  }
  .contact__role {
    font-size: 12px;
    color: var(--brand-red);
    margin-top: 3px;
  }
  .contact__address {
    font-size: 11.5px;
    line-height: 1.35;
    margin-top: 22px;
  }
  .contact__list {
    list-style: none;
    margin-top: 14px;
    font-size: 11.5px;
  }
  .contact__item {
    display: flex;
    align-items: center;
    gap: 8px;
    height: 18px;
  }
  .contact__icon {
    width: 14px; height: 14px;
    background: var(--brand-red);
    border-radius: 2px;
    display: flex; align-items: center; justify-content: center;
    flex: none;
  }
  .contact__icon svg { width: 10px; height: 10px; }
</style>
</head>
<body>

<section class="card card--front" aria-label="Business card front">
  <div class="brand"><span class="brand__mark"></span>KLV Roofing</div>
</section>

<section class="card card--back" aria-label="Business card back">
  <svg class="card__wave" viewBox="0 0 540 310" aria-hidden="true">
    <path d="M322,0 C270,80 276,222 150,310 L540,310 L540,0 Z" fill="var(--brand-red)"/>
    <path d="M332,0 C290,86 294,232 188,310 L540,310 L540,0 Z" fill="#ffffff"/>
    <path d="M336,0 C296,88 302,234 200,310 L540,310 L540,0 Z" fill="var(--card-black)"/>
  </svg>

  <div class="brand"><span class="brand__mark"></span>KLV Roofing</div>

  <div class="contact">
    <p class="contact__name">Daniel Reyes</p>
    <p class="contact__role">Managing Director</p>
    <p class="contact__address">PO BOX 480 Harbour Road<br>Unit 12 Etobicoke, ON</p>
    <ul class="contact__list">
      <li class="contact__item">
        <span class="contact__icon"><svg viewBox="0 0 10 10"><path d="M2,1 L4,1 L4.6,3 L3.5,3.8 Q4.5,5.8 6.2,6.5 L7,5.4 L9,6 L9,8 Q5,9 1.5,4.5 Q1,2.5 2,1Z" fill="#fff"/></svg></span>
        (416) 555 0172
      </li>
      <li class="contact__item">
        <span class="contact__icon"><svg viewBox="0 0 10 10"><rect x="2" y="1" width="6" height="3" fill="#fff"/><rect x="1" y="4.5" width="8" height="4" rx="1" fill="#fff"/></svg></span>
        (416) 555 0173
      </li>
      <li class="contact__item">
        <span class="contact__icon"><svg viewBox="0 0 10 10"><rect x="1" y="2.5" width="8" height="5" fill="none" stroke="#fff" stroke-width="1"/><path d="M1,2.5 L5,5.5 L9,2.5" fill="none" stroke="#fff" stroke-width="1"/></svg></span>
        info@klvroofing.ca
      </li>
      <li class="contact__item">
        <span class="contact__icon"><svg viewBox="0 0 10 10"><circle cx="5" cy="5" r="3.8" fill="none" stroke="#fff" stroke-width="0.9"/><ellipse cx="5" cy="5" rx="1.6" ry="3.8" fill="none" stroke="#fff" stroke-width="0.8"/><path d="M1.2,5 H8.8" stroke="#fff" stroke-width="0.8"/></svg></span>
        www.klvroofing.ca
      </li>
    </ul>
  </div>
</section>

</body>
</html>
```